20 year old business card needs re-design

We need to redesign our corporate business card look. We need something that appears more modern, eye catchy but professional.

Target Market(s)

manufacturing industry

Industry/Entity Type

Manufacturer

Contact Information for Business Card

One side can have the logo. Other side can have contact information.

Font styles to use
Serif

Colors
3277b5
33b8a4
ffffff

Requirements
Must have
• Eye catchy - need to standout from the crowd. company logo cannot change. Full name, job title, phone number and email address.
Should not have
• Fax, business address is not necessary.

```html
<!DOCTYPE html>
<html lang="en">
<head>
<meta charset="utf-8">
<title>Norvale Industrial – Business Card</title>
<link href="https://fonts.googleapis.com/css2?family=Lato:wght@400;700;900&display=swap" rel="stylesheet">
<style>
  :root {
    --stage: #2b2b2e;
    --brand-blue: #3277b5;
    --deep-blue: #2650ac;
    --mid-blue: #4a86cc;
    --pale-blue: #b9cdee;
    --mist: #dde6f5;
    --paper: #f4f6fa;
    --ink: #1d1d22;
    --ink-soft: #3a3a42;
    --accent-teal: #33b8a4;
  }
  * { box-sizing: border-box; margin: 0; padding: 0; }
  html, body {
    width: 1200px;
    height: 1031px;
    overflow: hidden;
    background: var(--stage);
    font-family: "Lato", sans-serif;
  }
  .stage {
    position: relative;
    width: 1200px;
    height: 1031px;
  }
  .card {
    position: absolute;
    top: 367px;
    width: 520px;
    height: 297px;
    border-radius: 4px;
    overflow: hidden;
    box-shadow: 0 12px 30px rgba(0,0,0,.45);
  }
  .card--front { left: 60px; }
  .card--back { left: 620px; background: var(--paper); }

  .blueprint-area {
    position: absolute;
    inset: 0;
  }
  .card--front .blueprint-area {
    background: linear-gradient(135deg, var(--deep-blue) 0%, var(--mid-blue) 55%, var(--deep-blue) 100%);
  }
  .card--back .blueprint-area {
    background: linear-gradient(160deg, var(--pale-blue) 0%, var(--mist) 55%, var(--paper) 85%);
  }

  .wordmark {
    position: absolute;
    display: flex;
    flex-direction: column;
    align-items: center;
    color: var(--ink);
  }
  .wordmark__name {
    font-weight: 900;
    font-size: 54px;
    letter-spacing: -1px;
    line-height: 1;
  }
  .wordmark__sub {
    font-weight: 900;
    font-size: 13px;
    letter-spacing: 11px;
    margin-top: 6px;
    margin-right: -11px;
  }
  .card--front .wordmark {
    left: 0; right: 0; top: 108px;
  }
  .card--back .wordmark {
    left: 40px; top: 60px;
  }
  .card--back .wordmark__name { font-size: 46px; }
  .card--back .wordmark__sub { font-size: 11px; letter-spacing: 9px; margin-right: -9px; }

  .holder {
    position: absolute;
    right: 30px;
    top: 92px;
    text-align: right;
  }
  .holder__name {
    font-size: 22px;
    font-weight: 900;
    color: var(--ink);
  }
  .holder__first { color: var(--brand-blue); }
  .holder__title {
    font-size: 13px;
    color: var(--ink-soft);
    margin-top: 2px;
  }

  .contact {
    position: absolute;
    left: 30px;
    bottom: 24px;
    list-style: none;
    font-size: 14px;
    color: var(--ink-soft);
  }
  .contact__row {
    display: flex;
    align-items: center;
    gap: 8px;
    line-height: 22px;
  }
  .contact__icon { width: 14px; height: 14px; flex: none; }
  .contact__web { font-weight: 700; color: var(--ink); }
  .contact__web span { color: var(--brand-blue); }
</style>
</head>
<body>
<main class="stage">

  <section class="card card--front" aria-label="Business card front">
    <div class="blueprint-area" role="img" aria-label="Blueprint-style technical drawing of gears and dimension lines in white on blue"></div>
    <div class="wordmark">
      <span class="wordmark__name">Norvale</span>
      <span class="wordmark__sub">INDUSTRIAL</span>
    </div>
  </section>

  <section class="card card--back" aria-label="Business card back">
    <div class="blueprint-area" role="img" aria-label="Faint blueprint-style technical drawing of gears fading to white"></div>
    <div class="wordmark">
      <span class="wordmark__name">Norvale</span>
      <span class="wordmark__sub">INDUSTRIAL</span>
    </div>

    <div class="holder">
      <p class="holder__name"><span class="holder__first">Dale</span> Merrin</p>
      <p class="holder__title">Senior Project Manager</p>
    </div>

    <ul class="contact">
      <li class="contact__row">
        <svg class="contact__icon" viewBox="0 0 14 14" aria-hidden="true">
          <circle cx="7" cy="7" r="7" fill="#3277b5"/>
          <path d="M4.5 3.5l1.5 0 .6 1.8-.9.7a5 5 0 0 0 2.3 2.3l.7-.9 1.8.6v1.5c-3.5.3-6.3-2.5-6-6z" fill="#fff"/>
        </svg>
        555-014-2800 xt 201
      </li>
      <li class="contact__row">
        <svg class="contact__icon" viewBox="0 0 14 14" aria-hidden="true">
          <circle cx="7" cy="7" r="7" fill="#3277b5"/>
          <rect x="3.5" y="4.5" width="7" height="5" fill="#fff"/>
          <path d="M3.5 4.5L7 7.3l3.5-2.8" fill="none" stroke="#3277b5" stroke-width=".8"/>
        </svg>
        dale@norvaleindustrial.com
      </li>
      <li class="contact__row">
        <svg class="contact__icon" viewBox="0 0 14 14" aria-hidden="true">
          <circle cx="7" cy="7" r="7" fill="#3277b5"/>
          <circle cx="7" cy="7" r="3.8" fill="none" stroke="#fff" stroke-width=".9"/>
          <path d="M3.2 7h7.6M7 3.2v7.6" stroke="#fff" stroke-width=".8"/>
        </svg>
        <span class="contact__web"><span>Norvale</span>Industrial.com</span>
      </li>
    </ul>
  </section>

</main>
</body>
</html>
```